Awsome new website

We are a Fencing Contracting company in Melbourne Australia. We supply and install Timer and Steel boundary fences as well as Pool fencing (e.g. glass, tubular steel). We also manufacture and install swing and sliding gates.

We want a new website that is a modern business website.
We are targeting domestic and business clients.
The design should compliment our logo and company name.
The website needs to be easy to update.

Some specifics we want.
Menu - Main menu at top of page and smaller footer menu (to add different menu items)
Slider - Main page to have a slider on it that's easy for us to add and remove slides.
Call to action - all pages to have a "call to action" logo or icon that attracts attention (see file "call_to_action.pdf)
Instant quote - we have a online quote page we need a distinctive logo or icon to redirect to this page.
Main page to have a product /Service guide (see file "website_idea.jpg")
Main page to have widgets or quick link to
o why choose us
o Brochures
o Gallery

Have a Gallery page formatted with different category galleries. e.g. Timber, Glass, Feature
Maintain the current link to our staff page with password, (link in footer menu)

Hopefully that covers everything.
Our current website is www.tallgumfencing.com.au to have a look at the current site.
regards Doug

• Turn off blogging as we don’t want 100’s of comments from spammers to delete

We would like to implement the Portalio plugin (see "http://portalio-plug.net/" ), but this can be done after the new Theme has been implemented.

```html
<!DOCTYPE html>
<html lang="en">
<head>
<meta charset="utf-8">
<title>Tall Gum Fencing</title>
<link href="https://fonts.googleapis.com/css2?family=Roboto+Condensed:wght@400;700&family=Montserrat:wght@400;500;600&family=Noto+Serif:ital,wght@1,400&family=Lato:wght@400;700&display=swap" rel="stylesheet">
<style>
:root{
  --red:#b01c22;
  --red-dark:#7d0f14;
  --red-deep:#5e0a0e;
  --orange-dark:#c8410f;
  --ink:#222;
  --body:#444;
  --nav:#111;
  --nav-active:#f4a51c;
  --line:#ddd;
  --white:#fff;
  --footer:#000;
  --footer-text:#bbb;
}
*{margin:0;padding:0;box-sizing:border-box}
html,body{width:929px;height:1200px;overflow:hidden;background:var(--white)}
body{position:relative;font-family:"Lato",Arial,sans-serif;color:var(--body)}
.abs{position:absolute}

.site-header{left:0;top:0;width:929px;height:82px;background:linear-gradient(#c4252b,var(--red-dark) 70%,var(--red-deep))}
.brand{left:102px;top:16px;display:flex;align-items:center;gap:8px}
.brand-mark{width:26px;height:26px;background:var(--white)}
.brand-name{font-family:"Roboto Condensed",sans-serif;font-weight:700;font-size:26px;color:var(--white);line-height:1}
.brand-tagline{left:102px;top:60px;font-family:"Roboto Condensed",sans-serif;font-weight:700;font-size:9.5px;color:var(--white);letter-spacing:.2px}
.office-call{right:104px;top:7px;color:var(--white);font-size:15px;font-family:"Montserrat",sans-serif;font-weight:500}
.office-call em{font-family:"Noto Serif",serif;font-size:12px;font-style:italic;font-weight:400}
.join-btn{left:642px;top:30px;width:185px;height:40px;background:linear-gradient(#ffb52a,#f09010);border-radius:3px;color:var(--white);font-family:"Roboto Condensed",sans-serif;font-weight:700;font-size:19px;display:flex;align-items:center;justify-content:center;box-shadow:0 2px 2px rgba(0,0,0,.3)}

.main-nav{left:0;top:82px;width:929px;height:36px;background:linear-gradient(#2a2a2a,var(--nav));display:flex;justify-content:center}
.main-nav a{font-family:"Montserrat",sans-serif;font-weight:500;font-size:11.5px;color:var(--white);text-decoration:none;padding:0 21px;line-height:36px;border-left:1px solid #333}
.main-nav a:first-child{border-left:0}
.main-nav a.active{color:var(--nav-active)}

.hero{left:0;top:118px;width:929px;height:386px;background:linear-gradient(100deg,#3b4a2a 0%,#6e7d4a 30%,#9a8a6a 55%,#7e9a4c 80%,#b48a3a 100%)}
.hero-arrow{top:288px;width:26px;height:26px;border-radius:50%;background:rgba(255,255,255,.75)}

.services{left:102px;top:542px;width:188px;height:410px;background:var(--red)}
.services h2{position:absolute;left:14px;top:12px;font-family:"Roboto Condensed",sans-serif;font-weight:700;font-size:18px;color:var(--white)}
.services .seal{position:absolute;left:30px;top:44px;width:128px;height:128px;border-radius:50%;background:var(--white)}
.services ul{position:absolute;left:15px;top:184px;list-style:none}
.services li{font-family:"Montserrat",sans-serif;font-weight:500;font-size:10px;color:var(--white);height:21.7px;display:flex;align-items:center;gap:6px;white-space:nowrap}

.quote-btn{left:102px;top:975px;width:188px;height:59px;background:linear-gradient(#ee6a1e,var(--orange-dark));border-radius:3px;box-shadow:0 2px 2px rgba(0,0,0,.3)}
.quote-btn .label{position:absolute;left:70px;top:6px;color:var(--white);font-family:"Montserrat",sans-serif;line-height:1}
.quote-btn .small{font-size:15px;font-weight:400;display:block}
.quote-btn .big{font-size:27px;font-weight:600;display:block;margin-top:2px}

.widget{top:540px;width:160px}
.widget h3{font-family:"Roboto Condensed",sans-serif;font-weight:700;font-size:17px;color:var(--ink)}
.widget .thumb{margin-top:9px;width:160px;height:127px;border:3px solid #e3e3e3}
.widget p{margin-top:11px;font-size:11px;line-height:16.8px;color:var(--body);height:112px}
.more{font-family:"Montserrat",sans-serif;font-size:10.5px;color:var(--red);text-decoration:none}

.divider{left:319px;top:859px;width:509px;height:1px;background:var(--line)}
.welcome{left:319px;top:879px;width:510px}
.welcome .pre{font-family:"Noto Serif",serif;font-style:italic;font-size:16px;color:var(--ink)}
.welcome h2{font-family:"Roboto Condensed",sans-serif;font-weight:700;font-size:20px;color:var(--red);line-height:1.1}
.welcome p{margin-top:12px;font-size:11px;line-height:16.8px}
.welcome .more{display:block;margin-top:11px}

.site-footer{left:0;top:1073px;width:929px;height:127px;background:var(--footer);font-family:"Montserrat",sans-serif}
.site-footer h4{font-size:12px;font-weight:500;color:var(--white)}
.site-footer .links{font-size:10.5px;color:var(--footer-text);margin-top:5px}
.site-footer .links span{margin:0 5px;color:#777}
.social{display:flex;gap:8px;margin-top:7px}
.social i{width:23px;height:23px;border-radius:50%;background:#888;display:block}
.copy{font-size:10.5px;color:var(--footer-text)}
</style>
</head>
<body>

<header class="abs site-header">
  <div class="abs brand"><span class="brand-mark"></span><span class="brand-name">Tall Gum Fencing</span></div>
  <div class="abs brand-tagline">WHEN QUALITY COUNTS, COUNT ON US</div>
  <div class="abs office-call"><em>Office Call Us</em> : 03 9472 6081</div>
  <a class="abs join-btn">JOIN NOW SUBSCRIBE</a>
</header>

<nav class="abs main-nav">
  <a class="active">HOME</a><a>STEELFORM</a><a>INSTANT QUOTE</a><a>GALLERY</a><a>PRODUCTS &amp; SERVICES</a><a>CONTACT US</a>
</nav>

<section class="abs hero" role="img" aria-label="Slider photo of a black wrought iron fence with spear tops in a green garden"></section>
<span class="abs hero-arrow" style="left:102px"></span>
<span class="abs hero-arrow" style="left:800px"></span>
<svg class="abs" style="left:102px;top:288px" width="26" height="26" aria-hidden="true"><path d="M15 8 L10 13 L15 18" stroke="#444" stroke-width="2.5" fill="none"/></svg>
<svg class="abs" style="left:800px;top:288px" width="26" height="26" aria-hidden="true"><path d="M11 8 L16 13 L11 18" stroke="#444" stroke-width="2.5" fill="none"/></svg>

<aside class="abs services">
  <h2>Our Services</h2>
  <span class="seal"></span>
  <ul>
    <li><svg width="12" height="12"><path d="M1 6 L5 10 L11 2" stroke="#fff" stroke-width="2" fill="none"/></svg>Bathroom Remodeling</li>
    <li><svg width="12" height="12"><path d="M1 6 L5 10 L11 2" stroke="#fff" stroke-width="2" fill="none"/></svg>Attic &amp; Garage Finishing</li>
    <li><svg width="12" height="12"><path d="M1 6 L5 10 L11 2" stroke="#fff" stroke-width="2" fill="none"/></svg>Carpentry</li>
    <li><svg width="12" height="12"><path d="M1 6 L5 10 L11 2" stroke="#fff" stroke-width="2" fill="none"/></svg>Tile &amp; Flooring</li>
    <li><svg width="12" height="12"><path d="M1 6 L5 10 L11 2" stroke="#fff" stroke-width="2" fill="none"/></svg>Decks</li>
    <li><svg width="12" height="12"><path d="M1 6 L5 10 L11 2" stroke="#fff" stroke-width="2" fill="none"/></svg>General Home Maintenance</li>
    <li><svg width="12" height="12"><path d="M1 6 L5 10 L11 2" stroke="#fff" stroke-width="2" fill="none"/></svg>Painting &amp; Wall Treatments</li>
    <li><svg width="12" height="12"><path d="M1 6 L5 10 L11 2" stroke="#fff" stroke-width="2" fill="none"/></svg>Drywall Install</li>
    <li><svg width="12" height="12"><path d="M1 6 L5 10 L11 2" stroke="#fff" stroke-width="2" fill="none"/></svg>Electrical</li>
    <li><svg width="12" height="12"><path d="M1 6 L5 10 L11 2" stroke="#fff" stroke-width="2" fill="none"/></svg>Fences</li>
  </ul>
</aside>

<a class="abs quote-btn">
  <svg class="abs" style="left:18px;top:11px" width="38" height="38" aria-hidden="true">
    <rect x="2" y="4" width="30" height="30" rx="4" fill="none" stroke="#fff" stroke-width="3"/>
    <path d="M14 24 L30 8 L35 13 L19 29 L13 30 Z" fill="#fff"/>
  </svg>
  <span class="label"><span class="small">INSTANT</span><span class="big">QUOTE</span></span>
</a>

<article class="abs widget" style="left:319px">
  <h3>Why Choose Us</h3>
  <div class="thumb" role="img" aria-label="Photo of two children standing behind a white picket fence" style="background:linear-gradient(#8aa0b8,#c9b98a)"></div>
  <p>We offer a 12 month workman ship warranty on our fences and will clean the site for free of any fencing debris from the fence construction upon completion of the job...</p>
  <a class="more">Find Out More ›</a>
</article>
<article class="abs widget" style="left:494px">
  <h3>Brochures</h3>
  <div class="thumb" role="img" aria-label="Photo of a spiral-bound green brochure" style="background:linear-gradient(135deg,#e8e8e6,#a9b54a)"></div>
  <p>No pool is complete without a beautiful Pool fence. See our range of Tubular Fencing designs Download our Steelform Fencing Brochure and see what a fantastic...</p>
  <a class="more">Download Here ›</a>
</article>
<article class="abs widget" style="left:668px">
  <h3>Gallery</h3>
  <div class="thumb" role="img" aria-label="Photo of a black iron gate in front of a house" style="background:linear-gradient(#9fb0c2,#b9a27c 55%,#4d5d3a)"></div>
  <p>Please feel free to look through our gallery, these are jobs that we have personally done! Please feel free to look through our gallery, these are jobs that we have personally done!...</p>
  <a class="more">See Our Work ›</a>
</article>

<div class="abs divider"></div>

<section class="abs welcome">
  <div class="pre">Welcome to</div>
  <h2>Tall Gum Fencing</h2>
  <p>Thank you for visiting us at Tall Gum Fencing, my name is Doug and I am the Manager.I built my first fence when I was in my early twenties and have been building fences ever since. Over the last few years we have spent the time looking for fantastic fencing contractors to join our team. Because we only accept the best we have built our business to be one of Victoria's largest fencing contractors.</p>
  <a class="more">Read More ›</a>
</section>

<footer class="abs site-footer">
  <div class="abs" style="left:102px;top:19px">
    <h4>Quick Links</h4>
    <div class="links">Home<span>|</span>Steelform<span>|</span>Instant Quote<span>|</span>Gallery<span>|</span>Products &amp; Services<span>|</span>Contact us</div>
    <h4 style="margin-top:15px">Gallery Links</h4>
    <div class="links">Timber<span>|</span>Glass</div>
  </div>
  <div class="abs" style="left:608px;top:19px">
    <h4>Get In Touch</h4>
    <div class="links">Office : 03 9472 6081</div>
    <div class="social"><i></i><i></i><i></i><i></i></div>
    <div class="copy" style="margin-top:14px">Copyright © 2013 Tall Gum Fencing.com.au</div>
  </div>
</footer>

</body>
</html>
```